New Modern floristry business design

Hi, we are a new business based in Sydney called "copper fern floristry"

With so many floristry's we need a good design that will set a great first impression.

A few descriptive words on how we envision copper fern floristry:

-dynamic design
-minimal colour (colour can be used to enhance the design)
-black white grey (can include gold,silver,metallic shadowing)
Strong "COPPER FERN" with a classy "FLORISTRY"
Bold with a touch of feminine

Copper Fern Floristry,
Delia Pruett,
Copperfernfloristry@mailvista.com.au

```html
<!DOCTYPE html>
<html lang="en">
<head>
<meta charset="utf-8">
<title>Copper Fern Floristry – Business Cards</title>
<link rel="stylesheet" href="https://fonts.googleapis.com/css2?family=Noto+Serif:wght@700&family=Cormorant+Garamond:ital,wght@1,500&family=Tinos:ital@1&display=swap">
<style>
  :root {
    --stage: #e4e4e4;
    --card-edge: #1c1c1c;
    --pattern-tone: #dcdcdc;
    --ink: #0a0a0a;
    --metal-dark: #050505;
    --metal-mid: #3a3a3a;
    --metal-light: #f2f2f2;
    --name-light: #f4f4f4;
  }
  html, body {
    margin: 0;
    padding: 0;
    width: 1200px;
    height: 1000px;
    overflow: hidden;
    background: var(--stage);
  }
  .canvas {
    position: relative;
    width: 1200px;
    height: 1000px;
  }
  .card {
    position: absolute;
    width: 730px;
    height: 445px;
    border-radius: 22px;
    border: 3px solid var(--card-edge);
    box-sizing: border-box;
    overflow: hidden;
  }
  .card--front { left: 38px; top: 42px; }
  .card--back  { left: 403px; top: 518px; }
  .card__pattern {
    position: absolute;
    inset: 0;
    background: var(--pattern-tone);
  }
  .card__panel {
    position: absolute;
    left: 37px;
    top: 52px;
    width: 648px;
    height: 343px;
    border-radius: 20px;
    background: conic-gradient(from 0deg at 50% 49%,
      var(--metal-dark) 0deg,
      var(--metal-light) 55deg,
      var(--metal-mid) 100deg,
      var(--metal-dark) 125deg,
      var(--metal-light) 185deg,
      var(--metal-dark) 240deg,
      var(--metal-light) 295deg,
      var(--metal-mid) 330deg,
      var(--metal-dark) 360deg);
    box-shadow: 0 0 12px rgba(0,0,0,0.45);
  }
  .wordmark {
    position: absolute;
    margin: 0;
    font-family: "Noto Serif", Georgia, serif;
    font-weight: 700;
    color: var(--ink);
    white-space: nowrap;
    line-height: 1;
  }
  .card--front .wordmark {
    left: 0;
    width: 100%;
    text-align: center;
  }
  .card--front .wordmark__main { top: 112px; font-size: 66px; }
  .card--front .wordmark__sub  { top: 210px; font-size: 66px; }
  .card--back .wordmark { left: 64px; }
  .card--back .wordmark__main { top: 72px; font-size: 40px; }
  .card--back .wordmark__sub  { top: 118px; font-size: 40px; }
  .holder-name {
    position: absolute;
    left: 40px;
    width: 648px;
    top: 290px;
    margin: 0;
    text-align: center;
    font-family: "Cormorant Garamond", "Times New Roman", serif;
    font-style: italic;
    font-weight: 500;
    font-size: 64px;
    line-height: 1;
    color: var(--name-light);
    text-shadow: 2px 2px 3px rgba(0,0,0,0.8);
  }
  .holder-email {
    position: absolute;
    left: 40px;
    width: 648px;
    top: 362px;
    margin: 0;
    text-align: center;
    font-family: "Tinos", "Times New Roman", serif;
    font-style: italic;
    font-size: 17px;
    color: var(--name-light);
  }
</style>
</head>
<body>
<main class="canvas">
  <section class="card card--front" aria-label="Business card front">
    <div class="card__pattern" role="img" aria-label="Black floral vine pattern on light grey"></div>
    <div class="card__panel"></div>
    <p class="wordmark wordmark__main">Copper Fern</p>
    <p class="wordmark wordmark__sub">Floristry</p>
  </section>

  <section class="card card--back" aria-label="Business card back">
    <div class="card__pattern" role="img" aria-label="Black floral vine pattern on light grey"></div>
    <div class="card__panel"></div>
    <p class="wordmark wordmark__main">Copper Fern</p>
    <p class="wordmark wordmark__sub">Floristry</p>
    <p class="holder-name">Delia Pruett</p>
    <p class="holder-email">Copperfernfloristry@mailvista.com.au</p>
  </section>
</main>
</body>
</html>
```